Flyer Design Project for lawn care business

I need a flyer designed for my lawn care business, "Fenwick's Upkeep Services".  It is a family owned small landscaping company. I was thinking something that I can print  2- 3 per page.
I have  2 different logos I can upload to give an idea.  I have seen some I like that are colorfull with neat graphics but I also like some that are simple and elegant.  I would like something that catches your eye and looks professionaly done.

Target Market(s)
Homeowners in Durham, North Carolina with homes usually valued $200,000 or more.
Industry/Entity Type
Landscaping
Requirements
Must have
- I would like the address of my website listed on it, www.fenwickupkeepservices-example.com
I would like for it to say somewhere, 50% off first service with seasonal service.
Not sure if I want to list some of the services that I offer or just say full service lawn care.
Nice to have
- I have a logo with a bull pushing a lawn mower.  I live in Durham, NC also known as the Bull City.  I am not in love with the logo so feel free to change it or not use it at all.

```html
<!DOCTYPE html>
<html lang="en">
<head>
<meta charset="utf-8">
<title>Fenwick's Upkeep Services – Flyer</title>
<link rel="stylesheet" href="https://fonts.googleapis.com/css2?family=Archivo+Black&family=Mulish:wght@700;800&family=Questrial&display=swap">
<style>
  :root {
    --page-bg: #f2f2f2;
    --card-bg: #ffffff;
    --card-edge: #2b2b2b;
    --grass-light: #5cc42a;
    --grass-mid: #3aa51b;
    --grass-deep: #23800f;
    --blade-light: #8fe23e;
    --blade-deep: #2f9412;
    --brand-green: #3b5a1f;
    --accent-green: #00e60a;
    --ink: #1c1c1c;
    --promo-text: #ffffff;
  }
  * { box-sizing: border-box; margin: 0; padding: 0; }
  html, body {
    width: 1200px;
    height: 932px;
    overflow: hidden;
    background: var(--page-bg);
  }
  .flyer {
    position: absolute;
    left: 15px;
    top: 55px;
    width: 1169px;
    height: 821px;
    background: var(--card-bg);
    border: 1.5px solid var(--card-edge);
    overflow: hidden;
  }
  .hero-photo {
    position: absolute;
    left: 0; top: 0;
    width: 100%;
    height: 226px;
    background:
      radial-gradient(ellipse 60% 80% at 75% 10%, var(--grass-light), transparent 70%),
      linear-gradient(180deg, var(--grass-mid) 0%, var(--grass-light) 45%, var(--grass-mid) 100%);
  }
  .promo {
    position: absolute;
    left: 58px;
    top: 28px;
    width: 300px;
    color: var(--promo-text);
    font-family: "Mulish", sans-serif;
    font-weight: 800;
    text-align: center;
    line-height: 0.95;
    transform: rotate(-12deg);
    transform-origin: center;
  }
  .promo-headline {
    display: block;
    font-family: "Questrial", sans-serif;
    font-size: 66px;
    letter-spacing: -1px;
    line-height: 0.95;
  }
  .promo-line {
    display: block;
    font-size: 36px;
  }
  .brand-panel {
    position: absolute;
    left: 0; top: 226px;
    width: 100%;
    height: 390px;
    text-align: center;
  }
  .brand-name {
    position: absolute;
    left: 0; right: 0;
    top: 36px;
    font-family: "Archivo Black", sans-serif;
    font-size: 128px;
    line-height: 1;
    letter-spacing: 4px;
    color: var(--brand-green);
  }
  .web-address {
    position: absolute;
    left: 0; right: 0;
    top: 187px;
    font-family: "Questrial", sans-serif;
    font-size: 33px;
    color: var(--ink);
  }
  .tagline {
    position: absolute;
    left: 0; right: 0;
    top: 240px;
    font-family: "Mulish", sans-serif;
    font-weight: 800;
    font-size: 84px;
    line-height: 1.1;
    color: var(--accent-green);
  }
  .grass-photo {
    position: absolute;
    left: 0; bottom: 0;
    width: 100%;
    height: 205px;
    background:
      radial-gradient(ellipse 50% 70% at 55% 100%, var(--blade-light), transparent 75%),
      linear-gradient(180deg, var(--blade-light) 0%, var(--grass-light) 40%, var(--blade-deep) 100%);
  }
</style>
</head>
<body>
  <main class="flyer">
    <section class="hero-photo" role="img" aria-label="Photo of a freshly mown green lawn with a yellow ride-on mower at the top edge">
      <p class="promo">
        <span class="promo-headline">50%OFF</span>
        <span class="promo-line">first service</span>
        <span class="promo-line">with seasonal</span>
        <span class="promo-line">service</span>
      </p>
    </section>

    <section class="brand-panel">
      <h1 class="brand-name">FENWICKS</h1>
      <p class="web-address">www.fenwickupkeepservices-example.com</p>
      <p class="tagline">full service lawn care</p>
    </section>

    <section class="grass-photo" role="img" aria-label="Close-up photo of bright green grass blades with a soft blurred background"></section>
  </main>
</body>
</html>
```